Letter and Envelope Design For Harborline Realty

Please design a letter and an envelope incorporating our logo (See Attached). We are also launched a business card contest. Since we want them to match, please feel free to submit a design for both the business card and also the letter design and envelope.

Requirements
Must have
• The envelope, the letter and the business cards must match somehow connecting the designs. We want them to have something that holds them together besides the logo.

```html
<!DOCTYPE html>
<html lang="en">
<head>
<meta charset="utf-8">
<title>Harborline Realty – Letterhead and Envelope</title>
<link href="https://fonts.googleapis.com/css2?family=Montserrat:wght@600&family=Open+Sans:wght@400;700&display=swap" rel="stylesheet">
<style>
  :root{
    --navy:#021a8c;
    --swoosh:#58595b;
    --paper:#ffffff;
    --backdrop:#e7e7e7;
    --ink:#3a3a3a;
    --heading:#1c1c1c;
  }
  *{margin:0;padding:0;box-sizing:border-box}
  html,body{width:1200px;height:825px;overflow:hidden;background:var(--backdrop)}
  .canvas{position:relative;width:1200px;height:825px}
  .piece{position:absolute;background:var(--paper);box-shadow:0 1px 4px rgba(0,0,0,.12)}
  .piece svg{position:absolute;left:0;display:block}
  .brand-name{position:absolute;left:0;right:0;text-align:center;font-family:"Montserrat",sans-serif;font-weight:600;color:var(--navy);letter-spacing:1.6px;font-size:12px}
  .contact{position:absolute;font-family:"Open Sans",sans-serif;color:#fff;font-size:6.6px;line-height:10px}
  .contact strong{font-weight:700}
  .contact.right{text-align:right}

  /* letter */
  .letter{left:80px;top:81px;width:470px;height:663px}
  .letter .brand-name{top:62px}
  .letter-body{position:absolute;left:40px;top:137px;width:390px;font-family:"Open Sans",sans-serif;color:var(--ink)}
  .greeting{font-family:"Open Sans",sans-serif;font-weight:700;font-size:10.5px;color:var(--heading);margin-bottom:18px}
  .letter-body p{font-size:9.2px;line-height:12.3px;text-align:justify;margin-bottom:12.3px}
  .signature{position:absolute;left:40px;top:488px;width:74px;height:34px;background:linear-gradient(90deg,#f1f1f1,#e4e4e4);border-radius:3px}
  .letter .contact{left:40px;top:622px}

  /* slip */
  .slip{left:617px;top:190px;width:469px;height:201px}
  .slip .brand-name{top:61px}
  .slip .contact.left{left:29px;top:8px}
  .slip .contact.right{right:29px;top:8px}

  /* envelope */
  .envelope{left:581px;top:424px;width:539px;height:320px;background:transparent;box-shadow:none}
  .envelope .brand-name{top:152px}
  .envelope .contact.left{left:46px;top:98px}
  .envelope .contact.right{right:40px;top:98px}
</style>
</head>
<body>
<main class="canvas">

  <!-- Letterhead -->
  <section class="piece letter" aria-label="Harborline Realty letterhead">
    <svg class="letter-header" width="470" height="100" viewBox="0 0 470 100" aria-hidden="true">
      <path d="M0 0H470V66Q235 30 0 66Z" fill="var(--navy)"/>
      <path d="M22 64Q235 12 448 64Q235 26 22 64Z" fill="var(--swoosh)" stroke="#fff" stroke-width="1.2"/>
      <circle cx="235" cy="37" r="22" fill="#fff" stroke="var(--navy)" stroke-width="3"/>
    </svg>
    <div class="brand-name">HARBORLINE REALTY</div>

    <div class="letter-body">
      <div class="greeting">Dear Mr. Ellis,</div>
      <p>Lorem Ipsum is simply dummy text of the printing and typesetting industry. Lorem Ipsum has been the industry's standard dummy text ever since the 1500s, when an unknown printer took a galley of type and scrambled it to make a type specimen book. It has survived not only five centuries, but also the leap into electronic typesetting, remaining essentially unchanged.</p>
      <p>The standard chunk of Lorem Ipsum used since the 1500s is reproduced below for those interested. Sections 1.10.32 and 1.10.33 from "de Finibus Bonorum et Malorum" by Orsino are also reproduced in their exact original form, accompanied by English versions from the 1914 translation by H. Penlow</p>
      <p>Lorem Ipsum is simply dummy text of the printing and typesetting industry. Lorem Ipsum has been the industry's standard dummy text ever since the 1500s, when an unknown printer took a galley of type and scrambled it to make a type specimen book. It has survived not only five centuries, but also the leap into electronic typesetting, remaining essentially unchanged. It was popularised in the</p>
      <p>The standard chunk of Lorem Ipsum used since the 1500s is reproduced below for those interested. Sections 1.10.32 and 1.10.33 from "de Finibus Bonorum et Malorum" by Orsino are also reproduced in their exact original form, accompanied by English versions from the 1914 translation by H. Penlow</p>
      <p>The standard chunk of Lorem Ipsum used since the 1500s is reproduced below for those interested. Sections 1.10.32 and 1.10.33 from "de Finibus Bonorum et Malorum" by Orsino are also reproduced in their exact original form.</p>
    </div>
    <div class="signature" role="img" aria-label="Handwritten signature"></div>

    <svg class="letter-footer" style="top:595px" width="470" height="68" viewBox="0 0 470 68" aria-hidden="true">
      <path d="M0 68H470V4Q235 68 0 4Z" fill="var(--navy)"/>
      <path d="M22 6Q235 70 448 6Q235 84 22 6Z" fill="var(--swoosh)" stroke="#fff" stroke-width="1.2"/>
      <circle cx="235" cy="39" r="20" fill="#fff" stroke="var(--navy)" stroke-width="3"/>
    </svg>
    <div class="contact"><strong>Harborline Realty</strong><br>Po. box 201, Street Name,<br>City Name, Zip Code - 00000</div>
  </section>

  <!-- Compliment slip -->
  <section class="piece slip" aria-label="Harborline Realty compliment slip">
    <svg width="469" height="90" viewBox="0 0 469 90" aria-hidden="true">
      <path d="M0 0H469V62Q234 30 0 62Z" fill="var(--navy)"/>
      <path d="M20 60Q234 10 449 60Q234 24 20 60Z" fill="var(--swoosh)" stroke="#fff" stroke-width="1.2"/>
      <circle cx="234" cy="36" r="22" fill="#fff" stroke="var(--navy)" stroke-width="3"/>
    </svg>
    <div class="brand-name">HARBORLINE REALTY</div>
    <div class="contact left"><strong>Harborline Realty</strong><br>Po. box 201, Street Name,<br>City Name, Zip Code - 00000</div>
    <div class="contact right">555-014-2290 ☎<br>info@harborlinerealty.com ✉<br>info@harborlinerealty.com ●</div>
  </section>

  <!-- Envelope -->
  <section class="piece envelope" aria-label="Harborline Realty envelope">
    <svg width="539" height="320" viewBox="0 0 539 320" aria-hidden="true">
      <path d="M0 84L12 40Q16 34 24 33L255 2Q270 0 285 2L515 33Q523 34 527 40L539 84Z" fill="var(--navy)"/>
      <rect x="0" y="84" width="539" height="236" fill="var(--paper)"/>
      <path d="M0 84H539V158Q270 110 0 158Z" fill="var(--navy)"/>
      <path d="M20 156Q270 86 519 156Q270 104 20 156Z" fill="var(--swoosh)" stroke="#fff" stroke-width="1.2"/>
      <circle cx="270" cy="128" r="22" fill="#fff" stroke="var(--navy)" stroke-width="3"/>
    </svg>
    <div class="brand-name">HARBORLINE REALTY</div>
    <div class="contact left"><strong>Harborline Realty</strong><br>Po. box 201, Street Name,<br>City Name, Zip Code - 00000</div>
    <div class="contact right">555-014-2290 ☎<br>info@harborlinerealty.com ✉<br>info@harborlinerealty.com ●</div>
  </section>

</main>
</body>
</html>
```